Heron Loan Partners Business Card

We need a business card design for our mortgage servicing company. In addition to servicing the loans of homeowners, we help homeowners with purchasing their homes and any mortgage refinancing. We would like to see designs that use the colors in the logo attached below (gold-ish yellow and navy blue), and any other design you deem fit! The design should communicate a simpler life with smart mortgages provided by Heron.

```html
<!DOCTYPE html>
<html lang="en">
<head>
<meta charset="utf-8">
<title>Heron Loan Partners – Business Card</title>
<link rel="stylesheet" href="https://fonts.googleapis.com/css2?family=Arimo:wght@400;700&display=swap">
<style>
  :root {
    --gold: #cfa43c;
    --navy: #221c4e;
    --card: #f7f7f8;
    --backdrop: #e4e4e4;
    --white: #ffffff;
  }
  * { box-sizing: border-box; margin: 0; padding: 0; }
  html, body {
    width: 1200px; height: 1200px; overflow: hidden;
    background: var(--backdrop);
    font-family: "Arimo", Arial, sans-serif;
  }
  .canvas { position: relative; width: 1200px; height: 1200px; }
  .card {
    position: absolute; left: 257px; width: 686px; height: 392px;
    background: var(--card); border-radius: 20px; overflow: hidden;
    box-shadow: 0 14px 26px rgba(0,0,0,0.18);
  }
  .card--front { top: 160px; }
  .card--back { top: 650px; }
  .card__swoosh { position: absolute; inset: 0; width: 100%; height: 100%; }

  .holder { position: absolute; left: 29px; top: 48px; }
  .holder__name { color: var(--gold); font-weight: 700; font-size: 26px; line-height: 1.1; }
  .holder__title { color: var(--navy); font-size: 17px; margin-top: 2px; }

  .brand-name { color: var(--gold); font-weight: 700; white-space: nowrap; }
  .card--front .brand-name { position: absolute; left: 30px; top: 182px; font-size: 27px; }

  .tagline { position: absolute; left: 30px; top: 346px; color: var(--navy); font-size: 16.5px; }

  .contact {
    position: absolute; right: 31px; top: 250px; text-align: right;
    color: var(--white); font-size: 16.5px; line-height: 21px;
  }
  .contact__address { margin-bottom: 14px; }
  .contact__line { display: flex; justify-content: flex-end; align-items: center; gap: 7px; height: 22px; }
  .contact__icon { width: 14px; height: 14px; flex: none; }

  .card--back .brand-name {
    position: absolute; left: 0; right: 0; top: 168px; text-align: center; font-size: 50px;
  }
  .card--back .website {
    position: absolute; left: 0; right: 0; top: 333px; text-align: center;
    color: var(--navy); font-size: 17px; letter-spacing: 3.5px;
  }
</style>
</head>
<body>
<main class="canvas">
  <section class="card card--front" aria-label="Business card front">
    <svg class="card__swoosh" viewBox="0 0 800 457" preserveAspectRatio="none" aria-hidden="true">
      <path fill="var(--navy)" d="M0,356 C250,370 560,322 782,0 L792,0 C568,336 250,378 0,364 Z"/>
      <path fill="var(--gold)" d="M0,364 C250,378 568,336 792,0 L800,0 L800,457 L0,457 Z"/>
    </svg>

    <div class="holder">
      <div class="holder__name">Daniel Price</div>
      <div class="holder__title">President</div>
    </div>

    <div class="brand-name">Heron Loan Partners</div>

    <p class="tagline">Simpler life with smart mortgages</p>

    <div class="contact">
      <div class="contact__address">4127 Harbor View Lane<br>Bayside, NY 11360</div>
      <div class="contact__line">(555) 0142-7789
        <svg class="contact__icon" viewBox="0 0 16 16" aria-hidden="true"><path fill="var(--navy)" d="M3.6 1.2l2.3 2.6-1.3 1.8c.9 2 2.6 3.7 4.6 4.6l1.8-1.3 2.6 2.3-1.3 2.6C7 13.6 2.4 9 1 3.8z"/></svg>
      </div>
      <div class="contact__line">name@Heron.com
        <svg class="contact__icon" viewBox="0 0 16 16" aria-hidden="true"><rect x="1" y="4" width="14" height="9" fill="var(--navy)"/><path d="M1.5 4.5L8 9.5l6.5-5" fill="none" stroke="var(--gold)" stroke-width="1.2"/></svg>
      </div>
      <div class="contact__line">www.Heron.com
        <svg class="contact__icon" viewBox="0 0 16 16" aria-hidden="true"><circle cx="8" cy="8" r="7" fill="var(--navy)"/><path d="M8 1v14M1 8h14" stroke="var(--gold)" stroke-width="1"/></svg>
      </div>
    </div>
  </section>

  <section class="card card--back" aria-label="Business card back">
    <div class="brand-name">Heron Loan Partners</div>
    <p class="website">www.Heron.com</p>
  </section>
</main>
</body>
</html>
```